Graphics Design of Physics Book

Hi
Size : 8" x 11.25"
We are education book Publication Company and would like to have book cover for "Physics" it has 4 volumes. All 4 having the same color scheme and design except the volume no.
Blue is my personal favorite but u can use any color. Want to have a band at the bottom of the cover to place our Logo “VORNA Education” a PDF of the same is attached, or you can place logo anywhere according to ur design.
I need “Physics” as title of the book to be visible prominently.
And volume and volume no. should also be Visible and eye catching I prefer a Graphic to enhance the Volume No.
A background pattern can also be a option (it should be vector form so that color can be change later)
Please do not offer any cut and paste design I need very professional presentation.
Volume and Number can be in metallic 3D (CMYK) effect.
only Professional presentation will get feedback.
I have provided a sample artwork for reference do not follow it but can be a reference what I needed !

Target Market(s)

Students Class 9th to 12th

Industry/Entity Type

Education

Font styles to use
Serif

Colors
3176b5
0555a3
85abd2
cadf82
abd036
9bcb3c

Requirements
Must have
• Eye catching.
• “Physics” as title of the book to be visible prominently.
• volume and volume no. should also be Visible and eye catching
• I prefer a Graphic to enhance the Volume No.
• Icons for
• 1. Questions and answers
• 2. Theory Notes
• 3. Tips & Tricks
• 4. Previous Year's Reference Questions
• 5. Covers Complete Syllabus
Nice to have
• decent seamless background or metallic 3d effect (not to be print in special Ink) design should only be in CMYK.
Should not have
• Physics related Pictures or Icons (Specially E=mc2) or any scientist photograph or I Need pure graphic design

```html
<!DOCTYPE html>
<html lang="en">
<head>
<meta charset="utf-8">
<title>Physics Volume 3 — Book Cover</title>
<link rel="stylesheet" href="https://fonts.googleapis.com/css2?family=Arvo&family=Archivo+Black&family=Oswald:wght@400&display=swap">
<style>
  :root {
    --indigo-deep: #2a1670;
    --indigo: #2d2585;
    --royal: #0555a3;
    --sky: #3176b5;
    --title-blue: #74c2ee;
    --extrude: #10141f;
    --ray: #ffffff;
    --band-light: #f2f2f2;
    --band-mid: #bdbdbd;
    --band-dark: #7a7a7a;
    --ink: #15151a;
  }
  html, body {
    margin: 0;
    padding: 0;
    width: 854px;
    height: 1200px;
    overflow: hidden;
    background: var(--indigo-deep);
  }
  .cover {
    position: relative;
    width: 854px;
    height: 1200px;
    overflow: hidden;
  }
  .cover-art {
    position: absolute;
    inset: 0;
    display: block;
  }
  .book-title {
    font-family: "Arvo", Georgia, serif;
    font-size: 178px;
    fill: var(--title-blue);
    letter-spacing: 4px;
  }
  .volume-word {
    font-family: "Archivo Black", "Arial Black", sans-serif;
    font-size: 134px;
  }
  .volume-number {
    font-family: "Archivo Black", "Arial Black", sans-serif;
    font-size: 900px;
  }
  .publisher {
    position: absolute;
    left: 302px;
    top: 986px;
    width: 246px;
    height: 80px;
    display: flex;
    flex-direction: column;
    align-items: center;
    justify-content: center;
    font-family: "Archivo Black", "Arial Black", sans-serif;
    color: var(--ink);
    line-height: 1;
  }
  .publisher-name { font-size: 40px; letter-spacing: 2px; }
  .publisher-sub { font-size: 20px; letter-spacing: 3px; margin-top: 4px; }
  .feature-band {
    position: absolute;
    left: 0;
    top: 1092px;
    width: 854px;
    height: 48px;
    background: linear-gradient(180deg, var(--band-dark) 0%, var(--band-light) 18%, #ffffff 45%, var(--band-mid) 85%, var(--band-dark) 100%);
    display: flex;
    align-items: center;
    justify-content: center;
    gap: 9px;
    margin: 0;
    padding: 0;
    list-style: none;
  }
  .feature {
    display: flex;
    align-items: center;
    gap: 6px;
    font-family: "Oswald", "Arial Narrow", sans-serif;
    font-size: 15px;
    color: var(--ink);
    white-space: nowrap;
  }
  .feature::before {
    content: "";
    width: 15px;
    height: 15px;
    border-radius: 50%;
    background: var(--title-blue);
    flex: none;
  }
</style>
</head>
<body>
<main class="cover">
  <svg class="cover-art" width="854" height="1200" viewBox="0 0 854 1200" xmlns="http://www.w3.org/2000/svg" aria-labelledby="cover-title">
    <title id="cover-title">Physics Volume 3</title>
    <defs>
      <linearGradient id="bg-sky" x1="0" y1="0" x2="0.35" y2="1">
        <stop offset="0" stop-color="#2a1670"/>
        <stop offset="0.35" stop-color="#2d2585"/>
        <stop offset="0.6" stop-color="#0a5aa8"/>
        <stop offset="0.85" stop-color="#6f9fd2"/>
        <stop offset="1" stop-color="#c9d8ee"/>
      </linearGradient>
      <radialGradient id="glow" cx="300" cy="1200" r="520" gradientUnits="userSpaceOnUse">
        <stop offset="0" stop-color="#ffffff"/>
        <stop offset="0.35" stop-color="#ffffff" stop-opacity="0.7"/>
        <stop offset="1" stop-color="#ffffff" stop-opacity="0"/>
      </radialGradient>
      <linearGradient id="footer-shade" x1="0" y1="0" x2="0" y2="1">
        <stop offset="0" stop-color="#2a1670" stop-opacity="0.9"/>
        <stop offset="1" stop-color="#c8d2ee" stop-opacity="0.8"/>
      </linearGradient>
      <linearGradient id="metal" x1="0" y1="0" x2="1" y2="0">
        <stop offset="0" stop-color="#6b6e78"/>
        <stop offset="0.3" stop-color="#f4f4f6"/>
        <stop offset="0.5" stop-color="#8d9099"/>
        <stop offset="0.75" stop-color="#e6e7ea"/>
        <stop offset="1" stop-color="#5e616a"/>
      </linearGradient>
    </defs>

    <rect class="backdrop" width="854" height="1200" fill="url(#bg-sky)"/>
    <g class="light-rays" fill="#ffffff" opacity="0.55">
      <polygon points="300,1200 0,860 0,900"/>
      <polygon points="300,1200 40,760 70,770"/>
      <polygon points="300,1200 250,700 268,700"/>
      <polygon points="300,1200 520,760 545,775"/>
      <polygon points="300,1200 854,980 854,1010"/>
      <polygon points="300,1200 854,860 854,880"/>
    </g>
    <rect class="glow" width="854" height="1200" fill="url(#glow)"/>
    <rect class="footer-shade" y="1140" width="854" height="60" fill="url(#footer-shade)"/>

    <line class="diagonal-rule" x1="140" y1="0" x2="318" y2="690" stroke="#111522" stroke-width="3"/>

    <text class="book-title" x="427" y="206" text-anchor="middle" textLength="742" lengthAdjust="spacingAndGlyphs">PHYSICS</text>

    <g class="volume-word" transform="translate(196 932) rotate(-90)">
      <text x="6" y="10" fill="#1b1b24" textLength="660" lengthAdjust="spacingAndGlyphs">VOLUME</text>
      <text x="0" y="0" fill="url(#metal)" textLength="660" lengthAdjust="spacingAndGlyphs">VOLUME</text>
    </g>

    <g class="volume-number">
      <text x="290" y="956" fill="var(--extrude)" textLength="500" lengthAdjust="spacingAndGlyphs">3</text>
      <text x="275" y="944" fill="var(--extrude)" textLength="500" lengthAdjust="spacingAndGlyphs">3</text>
      <text x="262" y="932" fill="var(--extrude)" textLength="500" lengthAdjust="spacingAndGlyphs">3</text>
      <text x="244" y="918" fill="var(--title-blue)" textLength="500" lengthAdjust="spacingAndGlyphs">3</text>
    </g>
  </svg>

  <div class="publisher">
    <span class="publisher-name">VORNA</span>
    <span class="publisher-sub">EDUCATION</span>
  </div>

  <ul class="feature-band">
    <li class="feature">Questions and answers</li>
    <li class="feature">Theory Notes</li>
    <li class="feature">Tips &amp; Tricks</li>
    <li class="feature">Previous Year's Reference Questions</li>
    <li class="feature">Covers Complete Syllabus</li>
  </ul>
</main>
</body>
</html>
```